2 sided Rack Card for Hotel Packages

Rack card advertising hotel packages - will need need to be front and back 3.5 x 8.5 - then will also need to be able to converted to an elevator poster 11x17. I have attached pictures but they are for examples or use they do NOT have to be used. Side 1 Headline: Plan your return Stay today!All packages include a Discount Special Rates*Spring Break Package (see attached image SpringBreakWaterparkM10) * All the following wording does not have to be used Package includes:Two Resort beach towelsTwo youth swim gogglesA $15 Parlotti's gift cardSpring Break Waterpark tote*Lunchbox Special Bramble Ridge Perks lunch bagPlastic lunch containerWater bottle* Fun in the Sun (see attached image FunInSun)Package includes:Two Resort beach towelsTwo youth swim gogglesTwo Resort sun visorsSunscreenFun in the Sun ToteToll Free Number: 800-317-5826 Website: www.resortatgovernorscrossing.comSide 2 - What's New for 2019*Sevierville ad is attached* Tidal Hollow Logo is attached *Heron Basin logo is attached Phone number: 800.317.5826 website: www.resortatgovernorscrossing.comAlso attached is the Resort Logo and artist rendition of Tidal Hollow

Target Market(s)

Guest that pick up Rack card in lobby

Industry/Entity Type

Hospitality

Requirements
Must have
• logo
• toll free
• website

```html
<!DOCTYPE html>
<html lang="en">
<head>
<meta charset="utf-8">
<title>Rack Card – Hotel Packages</title>
<link rel="stylesheet" href="https://fonts.googleapis.com/css2?family=Cinzel:wght@500;700&family=Raleway:ital,wght@0,300;0,500;0,700;1,500;1,600&family=Roboto:wght@700&family=Montserrat:ital,wght@1,700&display=swap">
<style>
  :root {
    --backdrop: #727272;
    --teal: #5b7f87;
    --teal-dark: #1f3552;
    --orange: #d89d5c;
    --brown: #86673f;
    --card-light: #f4f4f4;
    --card-mid: #d7d7d7;
    --white: #ffffff;
    --ink: #222222;
  }
  * { box-sizing: border-box; margin: 0; padding: 0; }
  html, body { width: 988px; height: 1200px; overflow: hidden; }
  body { background: var(--backdrop); position: relative; font-family: "Raleway", sans-serif; }

  .card { position: absolute; width: 329px; overflow: hidden; }
  .card--front { left: 139px; top: 181px; height: 800px; background: var(--teal); }
  .card--back { left: 536px; top: 181px; height: 819px; background: linear-gradient(var(--card-light), var(--card-mid)); }

  .layer { position: absolute; left: 0; width: 100%; }

  /* front */
  .package-title {
    position: absolute; left: 3px; right: 3px; height: 28px;
    background: var(--orange); color: var(--white);
    font: 700 18px/28px "Raleway", sans-serif; text-align: center;
  }
  .package-list {
    position: absolute; left: 0; right: 0; text-align: center; list-style: none;
    color: var(--white); font: 300 15.5px/19.5px "Raleway", sans-serif;
  }
  .hero-photo {
    top: 254px; height: 300px;
    background: linear-gradient(180deg, var(--teal) 0%, #3c5a74 35%, var(--teal-dark) 75%, #2d3f66 100%);
  }
  .front-lower { top: 0; height: 800px; }
  .brand {
    position: absolute; left: 0; right: 0; top: 520px;
    display: flex; align-items: center; justify-content: center; gap: 10px;
    color: var(--brown); font: 700 21px/1.1 "Cinzel", serif; text-align: center;
  }
  .brand__mark { width: 14px; height: 14px; background: var(--orange); flex: none; }
  .headline {
    position: absolute; left: 0; right: 0; top: 606px; text-align: center;
    color: var(--brown); font: 500 28px/25px "Cinzel", serif;
  }
  .fine-print {
    position: absolute; left: 0; right: 0; top: 692px; text-align: center;
    font: italic 700 11.5px/1 "Montserrat", sans-serif; color: var(--ink);
  }
  .phone {
    position: absolute; left: 0; right: 0; text-align: center;
    font: 700 44px/1 "Roboto", sans-serif; letter-spacing: 0.5px;
  }
  .web {
    position: absolute; left: 0; right: 0; text-align: center;
    font: 700 15.5px/1 "Roboto", sans-serif;
  }
  .card--front .phone { top: 720px; color: var(--brown); }
  .card--front .web { top: 762px; color: var(--brown); }

  /* back */
  .group-photo {
    top: 0; height: 300px;
    background: linear-gradient(160deg, #cfd6dc 0%, #b8a79a 40%, #d47a7a 70%, #c9c3bb 100%);
  }
  .whats-new {
    position: absolute; left: 0; right: 0; top: 324px; text-align: center;
    color: var(--brown); font: italic 500 22px/27.3px "Raleway", sans-serif;
  }
  .partner {
    position: absolute; left: 0; right: 0; text-align: center;
    display: flex; align-items: center; justify-content: center; gap: 8px;
    font: 700 26px/1 "Raleway", sans-serif;
  }
  .partner--hollow { top: 506px; color: #2aa3dc; }
  .partner--basin { top: 610px; color: var(--ink); }
  .partner__dot { width: 12px; height: 12px; border-radius: 50%; background: currentColor; }
  .card--back .phone { top: 733px; color: var(--white); }
  .card--back .web { top: 776px; color: var(--white); }
</style>
</head>
<body>

<section class="card card--front" aria-label="Rack card, packages side">
  <h2 class="package-title" style="top:4px">SPRING BREAK PACKAGE</h2>
  <ul class="package-list" style="top:50px">
    <li>Two Resort beach towels</li>
    <li>Two youth swim goggles</li>
    <li>A $15 Parlotti's gift card</li>
    <li>Splashline Lagoon tote</li>
  </ul>

  <h2 class="package-title" style="top:130px">LUNCHBOX SPECIAL</h2>
  <ul class="package-list" style="top:180px">
    <li>Bramble Ridge Perks lunch bag</li>
    <li>Plastic lunch container Water bottle*</li>
  </ul>

  <div class="layer hero-photo" role="img" aria-label="Photo of a girl cheering with arms raised as water splashes in the water park"></div>

  <h2 class="package-title" style="top:224px">FUN IN THE SUN</h2>
  <ul class="package-list" style="top:274px">
    <li>Two Resort beach towels</li>
    <li>Two youth swim goggles</li>
    <li>Two Resort sun visors</li>
    <li>Sunscreen</li>
  </ul>

  <svg class="layer front-lower" width="329" height="800" viewBox="0 0 329 800" aria-hidden="true">
    <defs>
      <linearGradient id="frontFade" x1="0" y1="0" x2="0" y2="1">
        <stop offset="0" stop-color="#f7f7f7"/>
        <stop offset="1" stop-color="#d4d4d4"/>
      </linearGradient>
    </defs>
    <polygon points="0,511 164,445 329,511 329,800 0,800" fill="url(#frontFade)"/>
  </svg>

  <div class="brand"><span class="brand__mark"></span><span>The Lodge<br>at Willow Bend Point</span></div>

  <h1 class="headline">Plan your return<br>Stay today!</h1>
  <p class="fine-print">All packages include a Discount Special Rates*</p>
  <p class="phone">800-317-5826</p>
  <p class="web">www.lodgeatwillowbendpoint.example</p>
</section>

<section class="card card--back" aria-label="Rack card, what's new side">
  <div class="layer group-photo" role="img" aria-label="Photo of three girls in swimsuits walking through the indoor water park"></div>

  <svg class="layer" style="top:0" width="329" height="819" viewBox="0 0 329 819" aria-hidden="true">
    <defs>
      <linearGradient id="backFade" x1="0" y1="0" x2="0" y2="1">
        <stop offset="0" stop-color="#f4f4f4"/>
        <stop offset="1" stop-color="#d6d6d6"/>
      </linearGradient>
    </defs>
    <polygon points="0,257 164,299 329,243 329,704 164,685 0,704" fill="url(#backFade)"/>
    <polyline points="0,257 164,299 329,243" fill="none" stroke="var(--brown)" stroke-width="6"/>
    <polygon points="0,704 164,685 329,718 329,819 0,819" fill="var(--teal)"/>
    <polyline points="0,704 164,685 329,718" fill="none" stroke="var(--brown)" stroke-width="5"/>
  </svg>

  <p class="whats-new">67 more Fully<br>Furnished Condos!<br>Heron Basin:<br>Featuring Firepits,<br>Hammock Area &amp;<br>Picnic Grounds</p>

  <p class="partner partner--hollow"><span class="partner__dot"></span>Tidal Hollow</p>
  <p class="partner partner--basin"><span class="partner__dot"></span>Heron Basin</p>

  <p class="phone">800-317-5826</p>
  <p class="web">www.lodgeatwillowbendpoint.example</p>
</section>

</body>
</html>
```